Single-sided business card for restaurant velmora with new logo made on this site

Business card options with new logo including restaurant name, address, phone number and website. This business card is single-sided only and will be presented at the hostess desk for clients to take. I would like to see options based on a cream card background, a white card background, a yellow card background and a burgundy colored background. It needs to be elegant and traditional.

Target Market(s)

local and international crowd

Industry/Entity Type

restaurant

Contact Information for Business Card

address, website and phone number

Font styles to use
Serif

Colors
EE7325
F08F49
F5BC92
FAE3D3
FDF4ED

Requirements
Must have
• new logo, address, phone number, website
Should not have
• more than three colors

```html
<!DOCTYPE html>
<html lang="es">
<head>
<meta charset="utf-8">
<title>Velmora – Tarjetas de presentación</title>
<link rel="stylesheet" href="https://fonts.googleapis.com/css2?family=Didact+Gothic&family=Mulish:wght@700&display=swap">
<style>
  :root {
    --backdrop: #ebebeb;
    --cream: #fdf9d6;
    --white: #f0eeee;
    --gold: #e2a428;
    --burgundy: #371819;
    --light: #ebe9e9;
    --ink: #3a1a1a;
  }
  * { margin: 0; padding: 0; box-sizing: border-box; }
  html, body { width: 1200px; height: 686px; overflow: hidden; }
  body {
    background: var(--backdrop);
    position: relative;
    font-family: "Didact Gothic", sans-serif;
  }
  .card {
    position: absolute;
    top: 168px;
    width: 188px;
    height: 330px;
    background: var(--card-bg);
    color: var(--card-text);
    text-align: center;
  }
  .card--cream   { left: 125px; --card-bg: var(--cream); --card-text: var(--ink); --mark: var(--ink); --banner-bg: var(--ink); --banner-text: #fff; --rule: var(--gold); }
  .card--white   { left: 375px; --card-bg: var(--white); --card-text: var(--ink); --mark: var(--gold); --banner-bg: var(--gold); --banner-text: var(--ink); --rule: var(--gold); }
  .card--gold    { left: 632px; --card-bg: var(--gold); --card-text: var(--ink); --mark: var(--ink); --banner-bg: var(--ink); --banner-text: var(--gold); --rule: var(--ink); }
  .card--burgundy{ left: 879px; top: 165px; height: 333px; --card-bg: var(--burgundy); --card-text: var(--light); --mark: var(--light); --banner-bg: var(--light); --banner-text: var(--ink); --rule: var(--light); }

  .brand-square {
    position: absolute;
    top: 40px;
    left: 50%;
    width: 57px;
    height: 57px;
    margin-left: -28.5px;
    background: var(--mark);
  }
  .brand-name {
    position: absolute;
    top: 108px;
    left: 0;
    right: 0;
    font-size: 25px;
    letter-spacing: 5px;
    padding-left: 5px;
    color: var(--card-text);
    line-height: 1;
  }
  .banner {
    position: absolute;
    top: 177px;
    left: 50%;
    width: 134px;
    margin-left: -67px;
    height: 14px;
    background: var(--banner-bg);
    color: var(--banner-text);
    font-family: "Mulish", sans-serif;
    font-weight: 700;
    font-size: 10px;
    line-height: 14px;
  }
  .address, .contact {
    position: absolute;
    left: 0;
    right: 0;
    font-size: 10.5px;
    line-height: 14.3px;
  }
  .address { top: 199px; }
  .divider {
    position: absolute;
    top: 251px;
    left: 50%;
    width: 34px;
    margin-left: -17px;
    height: 1px;
    background: var(--rule);
  }
  .contact { top: 262px; }
</style>
</head>
<body>
  <article class="card card--cream">
    <div class="brand-square"></div>
    <div class="brand-name">VELMORA</div>
    <div class="banner">Restaurant Velmora</div>
    <p class="address">Jacaranda 517<br>Bahía Serena,<br>Oaxaca CP 70945</p>
    <div class="divider"></div>
    <p class="contact">Reservaciones<br>958-555-0142<br>www.velmora.com.mx</p>
  </article>

  <article class="card card--white">
    <div class="brand-square"></div>
    <div class="brand-name">VELMORA</div>
    <div class="banner">Restaurant Velmora</div>
    <p class="address">Jacaranda 517<br>Bahía Serena,<br>Oaxaca CP 70945</p>
    <div class="divider"></div>
    <p class="contact">Reservaciones<br>958-555-0142<br>www.velmora.com.mx</p>
  </article>

  <article class="card card--gold">
    <div class="brand-square"></div>
    <div class="brand-name">VELMORA</div>
    <div class="banner">Restaurant Velmora</div>
    <p class="address">Jacaranda 517<br>Bahía Serena,<br>Oaxaca CP 70945</p>
    <div class="divider"></div>
    <p class="contact">Reservaciones<br>958-555-0142<br>www.velmora.com.mx</p>
  </article>

  <article class="card card--burgundy">
    <div class="brand-square"></div>
    <div class="brand-name">VELMORA</div>
    <div class="banner">Restaurant Velmora</div>
    <p class="address">Jacaranda 517<br>Bahía Serena,<br>Oaxaca CP 70945</p>
    <div class="divider"></div>
    <p class="contact">Reservaciones<br>958-555-0142<br>www.velmora.com.mx</p>
  </article>
</body>
</html>
```